New Business Card Design Project

I'd like a business card design around the same modern style that I used on my website www.brovanhs.com
It's gonna be one of those round corners double-sided business cards with maybe a big logo on the front and all the info on the back of the card.

Contact Information for Business Card

Marco Delgado
425-317-6084
www.brovanhs.com

www.facebook.com/BrovanHomeServices
www.intsgram.com/BrovanHomeServices

Requirements
Must have
• it needs to look elegant and modern

```html
<!DOCTYPE html>
<html lang="en">
<head>
<meta charset="utf-8">
<title>Brovan Home Services – Business Card</title>
<link rel="stylesheet" href="https://fonts.googleapis.com/css2?family=Work+Sans:wght@400;500;700&display=swap">
<style>
  :root {
    --backdrop: #e9e9ec;
    --ink: #2b2b2d;
    --ink-deep: #1c1c1e;
    --paper: #ffffff;
    --brand-blue: #1f8fd8;
    --muted: #e8e8ea;
  }
  * { box-sizing: border-box; margin: 0; padding: 0; }
  html, body {
    width: 1200px; height: 715px; overflow: hidden;
    background: var(--backdrop);
    font-family: "Work Sans", Arial, sans-serif;
  }
  .canvas {
    position: relative; width: 1200px; height: 715px;
    display: flex; align-items: center; justify-content: center; gap: 60px;
  }
  .card {
    position: relative; width: 520px; height: 297px;
    border-radius: 14px; overflow: hidden;
    box-shadow: 0 10px 28px rgba(0,0,0,.18);
  }
  /* Front */
  .card--front {
    background: var(--ink-deep);
    display: flex; align-items: center; justify-content: center;
  }
  .brand {
    display: flex; align-items: center; gap: 12px;
    color: var(--brand-blue); font-weight: 700;
  }
  .brand__dot {
    width: 16px; height: 16px; border-radius: 50%;
    background: var(--brand-blue); flex: none;
  }
  .brand__name { line-height: 1; white-space: nowrap; }
  .card--front .brand__name { font-size: 34px; letter-spacing: -0.3px; }
  /* Back */
  .card--back { background: var(--paper); }
  .card__waves { position: absolute; inset: 0; width: 100%; height: 100%; }
  .card--back .brand { position: absolute; left: 30px; top: 42px; }
  .card--back .brand__name { font-size: 28px; letter-spacing: -0.3px; }
  .card--back .brand__dot { width: 12px; height: 12px; }
  .person { position: absolute; right: 28px; top: 92px; text-align: right; }
  .person__name {
    color: var(--brand-blue); font-size: 20px; font-weight: 500; letter-spacing: 1.5px;
  }
  .person__title { color: var(--ink); font-size: 12px; margin-top: 2px; }
  .address {
    position: absolute; left: 28px; top: 222px;
    color: var(--muted); font-size: 12px; line-height: 1.5; font-style: normal;
  }
  .contacts {
    position: absolute; right: 20px; bottom: 12px;
    list-style: none; color: var(--muted); font-size: 11.5px; line-height: 1.5;
  }
  .contacts li { display: flex; align-items: center; justify-content: flex-end; gap: 9px; }
  .contacts svg { width: 10px; height: 10px; flex: none; }
  .icon-fill { fill: var(--brand-blue); }
  .icon-line { fill: none; stroke: var(--brand-blue); stroke-width: 1.6; }
</style>
</head>
<body>
<main class="canvas">
  <section class="card card--front" aria-label="Card front">
    <div class="brand">
      <span class="brand__dot"></span>
      <span class="brand__name">Brovan Home Services</span>
    </div>
  </section>

  <section class="card card--back" aria-label="Card back">
    <svg class="card__waves" viewBox="0 0 520 297" preserveAspectRatio="none" aria-hidden="true">
      <path fill="var(--brand-blue)" d="M0,126 C80,170 180,196 300,200 C180,205 80,188 0,160 Z"/>
      <path fill="var(--ink)" d="M120,168 C220,190 350,176 520,150 L520,158 C350,184 220,198 120,168 Z"/>
      <path fill="var(--ink)" d="M0,164 C90,196 200,206 330,202 C420,198 480,178 520,170 L520,297 L0,297 Z"/>
    </svg>

    <div class="brand">
      <span class="brand__dot"></span>
      <span class="brand__name">Brovan Home Services</span>
    </div>

    <div class="person">
      <p class="person__name">MARCO DELGADO</p>
      <p class="person__title">Director</p>
    </div>

    <address class="address">
      940 Maple Ridge Lane<br>Tulsa, OK 74105
    </address>

    <ul class="contacts">
      <li>425-317-6084
        <svg viewBox="0 0 10 10"><path class="icon-fill" d="M2,0.5 L3.6,0.5 L4.2,3 L3,3.8 C3.6,5.2 4.8,6.4 6.2,7 L7,5.8 L9.5,6.4 L9.5,8 C9.5,9 8.8,9.5 8,9.5 C4,9.2 0.8,6 0.5,2 C0.5,1.2 1,0.5 2,0.5 Z"/></svg>
      </li>
      <li>info@brovanhs.com
        <svg viewBox="0 0 10 10"><rect class="icon-line" x="0.8" y="2" width="8.4" height="6" rx="0.8"/><path class="icon-line" d="M1,2.4 L5,5.4 L9,2.4"/></svg>
      </li>
      <li>www.brovanhs.com
        <svg viewBox="0 0 10 10"><circle class="icon-line" cx="5" cy="5" r="4"/><path class="icon-line" d="M1,5 H9 M5,1 C3,3.5 3,6.5 5,9 M5,1 C7,3.5 7,6.5 5,9"/></svg>
      </li>
      <li>/BrovanHomeServices
        <svg viewBox="0 0 10 10"><circle class="icon-fill" cx="5" cy="5" r="4.2"/></svg>
      </li>
      <li>/BrovanHomeServices
        <svg viewBox="0 0 10 10"><rect class="icon-fill" x="1" y="1" width="8" height="8" rx="1.5"/></svg>
      </li>
    </ul>
  </section>
</main>
</body>
</html>
```